Sunset Harbor Living Web Page

We need a web page design that has two intro pages - first being a 'home page', then a link to the second page that has the 'content tabs' and a 'call to action' (see below).

The business helps people that wish to retire to S.E.Asia (Thailand, Malaysia, Indonesia,The Philippines etc) - to enjoy the lifestyle and the remaining years of their lives. What attracts S.E.Asia to many people is the lower cost, the atmoshpere and beauty of the tropics and the vibrancy of the various countries.

People that are wishing to make the most of their retirement and are adventurous at a great bargain compared to the cost of their own countries will be interested.

We help them achieve this - visa, financials (tax, gov't payments etc), introduce them to the right people for property, clubs, retirement facilities, insurance and so forth.

Therefore we are providing an extremely wide ranging service and this site will provide broad but general information only - with a call to action to come and see us for more specific information and how we can help them specifically.

This site will be predominantly for travel and lifestyle, it will be linked with another financial services (financial planning) site later down the track.

The colour scheme is dark green and blue - as per the attached logo design. Photos and background just think lifestyle and S.E.Asia - beaches/mountains/water/recreational activities for retirees.

Target market is mostly those coming up to retirement to those that are already retired. But we also expect to have some interest with younger people that would like to find out more and plan for the future. So a broad age group but I would say mostly 40-70 yrs old.

On the first (Home) page we would like our company name 'Sunset Harbor Living', our logo (which will be on all pages) and a statement such as: “Imagine a retirement where your dreams are brought to life, and you have never felt more alive. Let us show you how”. Then a link to the second page.

We would like an uncluttered site. On the second (contents) page the tabs would be:

- Visa
- Property
- Financials
- Travel
- Insurance & Healthcare
- Medical Tourism
- Cost of living
- Weekly Blogs and articles
- Sunset Harbor Living story

We would also like a call to action on the second page - asking them to leave their contact details if they wish to learn more or sign up to our weekly newsletter/blog.

We are open to suggestions and your imaginations.

Thank you
Malcolm

Font styles to use
Serif
Script

Colors
0255a3
3377b5
00a990
9bcb3c
abd036
33b8a4
85abd2
cadf82
86cfc6

Requirements
Must have
• I have been asked by the web designer to receive a 'Web Font' so that we can 'get off of Zentrofy'. Hope that makes sense.

```html
<!DOCTYPE html>
<html lang="en">
<head>
<meta charset="utf-8">
<title>Sunset Harbor Living</title>
<link rel="stylesheet" href="https://fonts.googleapis.com/css2?family=Roboto:wght@300;400;500;700&family=Roboto+Condensed:wght@400;700&display=swap">
<style>
:root{
  --green:#00a990;
  --teal:#17a98d;
  --lime:#a6cc3a;
  --lime-dark:#8cb22b;
  --blue:#0255a3;
  --blue-deep:#0d4fa0;
  --sky:#0aa6df;
  --sky-dark:#0288c4;
  --ink:#3c3c3c;
  --muted:#8a8a8a;
  --paper:#ffffff;
  --mist:#f3f4f4;
  --night:#1e1e1e;
}
*{box-sizing:border-box;margin:0;padding:0}
html,body{width:1200px;height:2616px;overflow:hidden}
body{position:relative;background:var(--paper);font-family:"Roboto",Arial,sans-serif;color:var(--ink)}
.abs{position:absolute}
a{color:inherit;text-decoration:none}

/* header */
.topline{left:0;top:0;width:1200px;height:5px;background:var(--green)}
.header{left:0;top:5px;width:1200px;height:96px;background:var(--paper)}
.brand{left:99px;top:30px;display:flex;align-items:center;gap:10px}
.brand-dot{width:34px;height:34px;border-radius:50%;background:var(--green)}
.brand-name{font-size:20px;font-weight:700;color:var(--blue)}
.contact{top:28px;display:flex;align-items:center;gap:14px}
.contact-icon{width:42px;height:42px;border-radius:50%;background:var(--lime);display:flex;align-items:center;justify-content:center}
.contact-text{font-size:12px;line-height:20px;color:#666}
.nav{left:0;top:101px;width:1200px;height:58px;background:linear-gradient(#14b3ea,var(--sky-dark))}
.nav ul{list-style:none;display:flex;justify-content:space-between;position:absolute;left:99px;right:99px;top:20px}
.nav li{font-size:13.5px;color:#fff;white-space:nowrap}

/* hero */
.hero{left:0;top:159px;width:1200px;height:464px;background:linear-gradient(#c29a72 0%,#8e6f5a 35%,#5b5d54 60%,#3d4a40 100%)}
.hero-title{left:0;top:290px;width:1200px;text-align:center;font-family:"Roboto Condensed",Arial,sans-serif;font-weight:700;font-size:33px;line-height:52px;color:#fff;text-transform:uppercase;letter-spacing:.3px}
.hero-btn{left:455px;top:434px;width:272px;height:47px;border:2px solid #fff;border-radius:24px;color:#fff;font-family:"Roboto Condensed",Arial,sans-serif;font-size:23px;text-align:center;line-height:43px}
.hero-arrow{top:377px;width:38px;height:38px;border:2px solid rgba(255,255,255,.7);border-radius:50%}

/* welcome */
.welcome{left:0;top:623px;width:1200px;height:280px;background:var(--teal)}
.welcome h1{position:absolute;top:42px;width:1200px;text-align:center;font-weight:400;font-size:30px;color:#fff;letter-spacing:.5px}
.welcome p{position:absolute;left:238px;width:724px;top:96px;text-align:center;font-size:12px;line-height:21px;color:#e9f7f3}
.pill{display:flex;align-items:center;justify-content:space-between;border-radius:22px}
.pill .go{border-radius:50%;display:flex;align-items:center;justify-content:center}
.welcome .pill{position:absolute;left:521px;top:186px;width:157px;height:42px;border:2px solid #fff;padding-left:22px;padding-right:2px;color:#fff;font-size:15px}
.welcome .go{width:38px;height:38px;background:#fff}
.notch{left:586px;top:889px;width:0;height:0;border-left:14px solid transparent;border-right:14px solid transparent;border-bottom:14px solid var(--paper)}

/* service cards */
.card{top:956px;width:318px;height:422px;background:#f9f9f9;border:3px solid #eeeeee}
.card-img{position:absolute;left:15px;top:14px;width:282px;height:162px}
.card h2{position:absolute;top:208px;width:100%;text-align:center;font-weight:400;font-size:20px;color:#444;letter-spacing:.5px}
.card p{position:absolute;left:22px;right:22px;top:246px;text-align:center;font-size:11.5px;line-height:21px;color:var(--muted)}
.card .pill{position:absolute;left:98px;top:347px;width:116px;height:36px;border:2px solid var(--green);padding-left:12px;padding-right:1px;color:var(--green);font-size:11.5px}
.card .go{width:31px;height:31px;background:var(--green)}

/* travel */
.travel-img{left:0;top:1430px;width:603px;height:429px;background:linear-gradient(160deg,#9cc7c4 0%,#6f8a62 40%,#5d4a3c 70%,#33422a 100%)}
.slide-arrow{top:1459px;width:22px;height:22px;border:1.5px solid rgba(255,255,255,.8);border-radius:50%}
.travel{left:603px;top:1430px;width:597px;height:429px;background:linear-gradient(135deg,#1557a8,#0a4a99)}
.travel h2{position:absolute;left:45px;top:36px;font-weight:400;font-size:24px;color:#fff}
.travel .sub{position:absolute;left:48px;top:76px;font-size:14px;color:#e5ecf7}
.travel p{position:absolute;left:49px;width:452px;font-size:11.5px;line-height:21px;color:#dfe8f5}
.travel .pill{position:absolute;left:49px;top:338px;width:156px;height:42px;border:2px solid #fff;padding-left:22px;padding-right:2px;color:#fff;font-size:15px}
.travel .go{width:36px;height:36px;border:2px solid #fff}

/* insurance */
.care{left:0;top:1859px;width:1200px;height:394px;background:var(--mist)}
.care h2{position:absolute;top:44px;width:1200px;text-align:center;font-weight:400;font-size:28px;color:#444}
.feature{top:1978px;width:320px;text-align:center}
.feature-icon{width:90px;height:90px;margin:0 auto;border-radius:50%;border:4px solid #fff;box-shadow:0 0 0 1px #dcdcdc;display:flex;align-items:center;justify-content:center}
.feature h3{margin-top:32px;font-weight:500;font-size:16px;color:#333;letter-spacing:.3px}
.feature p{margin-top:10px;font-size:12px;line-height:21px;color:var(--muted)}

/* newsletter */
.newsletter{left:197px;top:2215px;width:806px;height:73px;background:var(--lime)}
.newsletter .label{position:absolute;left:59px;top:24px;font-size:22px;color:#fff;letter-spacing:.3px}
.newsletter .field{position:absolute;left:358px;top:14px;width:361px;height:45px;border:1.5px solid rgba(255,255,255,.85);border-radius:23px}
.newsletter .send{position:absolute;right:-1px;top:2px;width:122px;height:38px;border-radius:20px;background:var(--lime-dark);color:#fff;font-size:16px;text-align:center;line-height:38px}

/* footer */
.footer{left:0;top:2253px;width:1200px;height:293px;background:var(--night)}
.footer-brand{left:143px;top:2360px;width:240px;text-align:center}
.footer-brand .mark{width:110px;height:110px;margin:0 auto 14px;border-radius:50%;background:#fff}
.footer-brand .name{font-size:25px;font-weight:700;color:#fff}
.footer h4{position:absolute;top:2330px;font-weight:400;font-size:16px;color:#fff;letter-spacing:.3px}
.footer-contact{left:485px;top:2374px;width:260px;font-size:11.5px;line-height:21px;color:#8f8f8f}
.footer-contact div{margin-bottom:9px}
.links{list-style:none;top:2374px;font-size:11.5px;color:#8f8f8f}
.links li{height:29.7px}
.links li::before{content:"›";margin-right:10px;color:#8f8f8f}
.bottombar{left:0;top:2546px;width:1200px;height:70px;background:linear-gradient(#12ade6,var(--sky-dark))}
.social{top:2564px;width:28px;height:28px;border:1.5px solid #fff;border-radius:50%}
.copyright{right:96px;top:2570px;font-size:13px;color:#fff}
</style>
</head>
<body>

<div class="abs topline"></div>
<header class="abs header"></header>
<div class="abs brand"><span class="brand-dot"></span><span class="brand-name">Sunset Harbor Living</span></div>

<div class="abs contact" style="left:675px">
  <span class="contact-icon"><svg width="20" height="20" viewBox="0 0 24 24"><path d="M6.6 10.8a15 15 0 0 0 6.6 6.6l2.2-2.2c.3-.3.7-.4 1-.2 1.1.4 2.3.6 3.6.6.6 0 1 .4 1 1V20c0 .6-.4 1-1 1A17 17 0 0 1 3 4c0-.6.4-1 1-1h3.5c.6 0 1 .4 1 1 0 1.3.2 2.5.6 3.6.1.3 0 .7-.2 1z" fill="#fff"/></svg></span>
  <span class="contact-text">CALL US ON :<br>(000) - 5550142876</span>
</div>
<div class="abs contact" style="left:891px">
  <span class="contact-icon"><svg width="20" height="20" viewBox="0 0 24 24"><rect x="3" y="5" width="18" height="14" rx="2" fill="none" stroke="#fff" stroke-width="2"/><path d="M3 7l9 6 9-6" fill="none" stroke="#fff" stroke-width="2"/></svg></span>
  <span class="contact-text">MAIL US ON :<br>info@sunsetharbor.example</span>
</div>

<nav class="abs nav">
  <ul>
    <li>Home</li><li>Visa</li><li>Property</li><li>Financials</li><li>Travel</li><li>Insurance &amp; Healthcare</li><li>Medical Tourism</li><li>Cost of living</li><li>Weekly Blogs and articles</li><li>Sunset Harbor Living story</li><li>Contact us</li>
  </ul>
</nav>

<section class="abs hero" role="img" aria-label="Temple pagodas beside a lake at sunset"></section>
<div class="abs hero-title">Imagine a retirement where your dreams are<br>brought to life, and you have never felt more alive</div>
<a class="abs hero-btn">Let us show you how</a>
<span class="abs hero-arrow" style="left:30px"><svg width="34" height="34" viewBox="0 0 34 34"><path d="M20 10l-7 7 7 7" fill="none" stroke="#fff" stroke-width="2"/></svg></span>
<span class="abs hero-arrow" style="left:1125px"><svg width="34" height="34" viewBox="0 0 34 34"><path d="M14 10l7 7-7 7" fill="none" stroke="#fff" stroke-width="2"/></svg></span>

<section class="abs welcome">
  <h1>WELCOME TO SUNSET HARBOR LIVING</h1>
  <p>It is a long established fact that a reader will be distracted by the readable content of a page when looking at its layout. The point of using Lorem Ipsum is that it has a more-or-less normal distribution of letters, as opposed to using 'Content here, content here', making it look like readable English. Many desktop publishing packages and web page editors now use Lorem Ipsum as their default model</p>
  <a class="pill">Learn More <span class="go"><svg width="14" height="14" viewBox="0 0 14 14"><path d="M3 3l4 4-4 4M7 3l4 4-4 4" fill="none" stroke="#17a98d" stroke-width="1.8"/></svg></span></a>
</section>
<div class="abs notch"></div>

<article class="abs card" style="left:99px">
  <div class="card-img" role="img" aria-label="Floating lanterns over a temple at night" style="background:linear-gradient(#141a2e,#3a2a22 70%,#c7702a)"></div>
  <h2>VISA</h2>
  <p>There are many variations of passages of Lorem Ipsum available, but the majority have suffered alteration in some form, by injected humour, or randomised words which don't look even slightly</p>
  <a class="pill">Learn More <span class="go"><svg width="12" height="12" viewBox="0 0 14 14"><path d="M3 3l4 4-4 4M7 3l4 4-4 4" fill="none" stroke="#fff" stroke-width="1.8"/></svg></span></a>
</article>
<article class="abs card" style="left:441px">
  <div class="card-img" role="img" aria-label="Elephant ride in a green tropical park" style="background:linear-gradient(#6fb4e6 0%,#a9d1ec 40%,#5d9a3c 65%,#3f7a28)"></div>
  <h2>PROPERTY</h2>
  <p>There are many variations of passages of Lorem Ipsum available, but the majority have suffered alteration in some form, by injected humour, or randomised words which don't look even slightly</p>
  <a class="pill">Learn More <span class="go"><svg width="12" height="12" viewBox="0 0 14 14"><path d="M3 3l4 4-4 4M7 3l4 4-4 4" fill="none" stroke="#fff" stroke-width="1.8"/></svg></span></a>
</article>
<article class="abs card" style="left:783px">
  <div class="card-img" role="img" aria-label="Mountain top pagodas over a valley" style="background:linear-gradient(#4f8fd0 0%,#c9c0b8 50%,#7d7a64 75%,#3f5a33)"></div>
  <h2>FINANCIALS</h2>
  <p>There are many variations of passages of Lorem Ipsum available, but the majority have suffered alteration in some form, by injected humour, or randomised words which don't look even slightly</p>
  <a class="pill">Learn More <span class="go"><svg width="12" height="12" viewBox="0 0 14 14"><path d="M3 3l4 4-4 4M7 3l4 4-4 4" fill="none" stroke="#fff" stroke-width="1.8"/></svg></span></a>
</article>

<div class="abs travel-img" role="img" aria-label="Hillside temple towers among tropical trees"></div>
<span class="abs slide-arrow" style="left:516px"><svg width="19" height="19" viewBox="0 0 19 19"><path d="M11 5l-4 4.5 4 4.5" fill="none" stroke="#fff" stroke-width="1.5"/></svg></span>
<span class="abs slide-arrow" style="left:543px"><svg width="19" height="19" viewBox="0 0 19 19"><path d="M8 5l4 4.5-4 4.5" fill="none" stroke="#fff" stroke-width="1.5"/></svg></span>
<section class="abs travel">
  <h2>Travel to Malaysia</h2>
  <div class="sub">To Enjoy The Lifestyle And The Remaining Years Of Their Lives.</div>
  <p style="top:116px">Sed ut perspiciatis unde omnis iste natus error sit voluptatem accusantium doloremque laudantium, totam rem aperiam, eaque ipsa quae ab illo inventore veritatis et quasi architecto beatae vitae dicta sunt explicabo. Nemo enim ipsam voluptatem quia voluptas sit aspernatur aut odit aut fugit, sed quia consequuntur magni dolores eos qui ratione voluptatem sequi nesciunt.</p>
  <p style="top:239px">Neque porro quisquam est, qui dolorem ipsum quia dolor sit amet, consectetur, adipisci velit, sed quia non numquam eius modi tempora incidunt ut labore et dolore magnam aliquam quaerat voluptatem.</p>
  <a class="pill">Learn More <span class="go"><svg width="12" height="12" viewBox="0 0 14 14"><path d="M3 3l4 4-4 4M7 3l4 4-4 4" fill="none" stroke="#fff" stroke-width="1.8"/></svg></span></a>
</section>

<section class="abs care"><h2>INSURANCE &amp; HEALTHCARE</h2></section>
<div class="abs feature" style="left:81px">
  <div class="feature-icon" style="background:#86cfc6"><svg width="40" height="40" viewBox="0 0 40 40"><circle cx="20" cy="20" r="13" fill="none" stroke="#fff" stroke-width="2.5"/><path d="M26 14l-4 8-8 4 4-8z" fill="#fff"/></svg></div>
  <h3>FINIBUS BONORUM</h3>
  <p>Sed ut perspiciatis unde omnis iste natus error sit voluptatem accusantium doloremque laudantium, totam rem aperiam, eaque ipsa quae</p>
</div>
<div class="abs feature" style="left:440px">
  <div class="feature-icon" style="background:#85abd2"><svg width="40" height="40" viewBox="0 0 40 40"><path d="M8 18a12 12 0 0 1 24 0z" fill="#fff"/><rect x="19" y="18" width="2.5" height="14" fill="#fff"/><rect x="10" y="31" width="20" height="2.5" fill="#fff"/></svg></div>
  <h3>FINIBUS BONORUM</h3>
  <p>Sed ut perspiciatis unde omnis iste natus error sit voluptatem accusantium doloremque laudantium, totam rem aperiam, eaque ipsa quae</p>
</div>
<div class="abs feature" style="left:801px">
  <div class="feature-icon" style="background:#abd036"><svg width="40" height="40" viewBox="0 0 40 40"><rect x="7" y="13" width="26" height="18" rx="3" fill="#fff"/><rect x="14" y="9" width="10" height="5" rx="1" fill="#fff"/><circle cx="20" cy="22" r="5" fill="#abd036"/><circle cx="20" cy="22" r="2.5" fill="#fff"/></svg></div>
  <h3>FINIBUS BONORUM</h3>
  <p>Sed ut perspiciatis unde omnis iste natus error sit voluptatem accusantium doloremque laudantium, totam rem aperiam, eaque ipsa quae</p>
</div>

<footer class="abs footer"></footer>
<div class="abs newsletter">
  <span class="label">NEWSLETTER SIGN UP</span>
  <div class="field"><span class="send">SEND NOW</span></div>
</div>

<div class="abs footer-brand"><div class="mark"></div><div class="name">Sunset Harbor Living</div></div>
<h4 style="left:485px">GET IN TOUCH</h4>
<div class="abs footer-contact">
  <div>Address : 200 Latin words, combined with a handful of model sentence structures</div>
  <div>Phone No : (000) - 555014287</div>
  <div>Mail Id : info@sunsetharbor.example</div>
  <div>Fax : (000) - 5550142870</div>
</div>
<h4 style="left:830px">INFORMATION</h4>
<ul class="abs links" style="left:830px"><li>Home</li><li>Visa</li><li>Property</li><li>Financials</li><li>Travel</li></ul>
<ul class="abs links" style="left:949px"><li>Insurance &amp; Healthcare</li><li>Medical Tourism</li><li>Cost of living</li><li>Weekly Blogs and articles</li><li>Sunset Harbor Living story</li></ul>

<div class="abs bottombar"></div>
<span class="abs social" style="left:99px"></span>
<span class="abs social" style="left:138px"></span>
<span class="abs social" style="left:176px"></span>
<div class="abs copyright">Copyrights@2016Company Name All rights reserved</div>

</body>
</html>
```